KAJU Freightways #ALLKAJU Business Cards & Letterhead

I am looking to business cards designed for our organization. We are currently undergoing a small re-branding that is taking place. Our organization is called KAJU Freightways and we are headquartered in Phoenix, AZ. We primarily provide transportation and logistics services to the Marlow Parcel Bureau who is our largest customer. I would like to see a design that incorporates name, title, contact info, website, and address (this will be different depending on the employee). I would also like to see some color on the business card using our logo colors or a variation. I would like our logo on the back of the business card with the website displayed. The final design should communicate that we are a next generation transportation operate that focuses on being driver-first, customer-centric, innovative, and sustainable.We would also like our #ALLKAJU catch phrase incorporated as well.

Target Market(s)

Transportation & Logistics

Industry/Entity Type

Trucking Company

Contact Information for Business Card

-First and Last Name
-Position Title
-Contact Phone
-Contact Email
-Physical Address

Font styles to use
Serif

Colors

Designer to choose colors to be used in the design.

Requirements
Must have
• -KAJU logo prominently displayed
• -#ALLKAJU catch phrase used
• -Some amount of color, design gradient, etc.
• -Logo on the back with website listed (https://www.kajufreightco.example)

```html
<!DOCTYPE html>
<html lang="en">
<head>
<meta charset="utf-8">
<title>KAJU Freightways – Business Cards &amp; Letterhead</title>
<link rel="stylesheet" href="https://fonts.googleapis.com/css2?family=Source+Serif+4:wght@400;600;700&display=swap">
<style>
  :root {
    --backdrop: #999999;
    --paper: #ffffff;
    --green: #82c341;
    --navy: #0d3340;
    --grey-text: #666666;
    --rule: #bfbfbf;
  }
  * { margin: 0; padding: 0; box-sizing: border-box; }
  html, body { width: 1200px; height: 763px; overflow: hidden; }
  body {
    background: var(--backdrop);
    font-family: "Source Serif 4", Georgia, serif;
    position: relative;
  }
  .card {
    position: absolute;
    left: 91px;
    width: 399px;
    height: 234px;
    border-radius: 8px;
    overflow: hidden;
    border: 1px solid #7a7a7a;
  }
  .card-front { top: 134px; background: var(--paper); }
  .card-back { top: 390px; background: var(--green); }

  .brand-name {
    position: absolute;
    display: flex;
    align-items: center;
    justify-content: center;
    gap: 6px;
    font-weight: 700;
    line-height: 1;
    white-space: nowrap;
  }
  .brand-square { flex: none; }
  .card-front .brand-name {
    left: 27px; top: 88px; width: 166px; height: 40px;
    color: var(--navy); font-size: 30px;
  }
  .card-front .brand-square { width: 10px; height: 10px; background: var(--green); }
  .card-back .brand-name {
    left: 0; right: 0; top: 94px; height: 46px;
    color: var(--paper); font-size: 38px; gap: 8px;
  }
  .card-back .brand-square { width: 12px; height: 12px; background: var(--paper); }

  .brand-tagline {
    position: absolute;
    font-weight: 600;
    color: var(--green);
    white-space: nowrap;
    text-align: center;
  }
  .card-front .brand-tagline { left: 27px; top: 138px; width: 166px; font-size: 10px; }

  .divider {
    position: absolute; left: 199px; top: 65px;
    width: 1px; height: 102px; background: var(--rule);
  }
  .contact { position: absolute; left: 214px; top: 63px; color: var(--grey-text); }
  .contact-name { font-size: 13.5px; font-weight: 700; color: var(--navy); line-height: 16px; }
  .contact-title { font-size: 9.5px; color: var(--green); line-height: 12px; margin-bottom: 8px; }
  .contact-address { font-size: 9.5px; line-height: 12px; margin-bottom: 7px; }
  .contact-line { display: flex; align-items: center; gap: 3px; font-size: 9.5px; line-height: 13px; }
  .icon { width: 8px; height: 8px; flex: none; }

  .hashtag-band {
    position: absolute; left: 0; right: 0; bottom: 0;
    height: 23px;
    background: var(--green);
    border-top: 2px solid var(--navy);
    color: var(--paper);
    font-weight: 700;
    font-size: 10px;
    display: flex; align-items: center; justify-content: center;
  }
  .card-back .website {
    position: absolute; left: 0; right: 0; top: 205px;
    text-align: center; color: var(--paper); font-size: 11px;
  }

  .letterhead {
    position: absolute; left: 523px; top: 17px;
    width: 570px; height: 725px;
    background: var(--paper);
    border: 1px solid #7a7a7a;
  }
  .letterhead .brand-name {
    left: 0; right: 0; top: 38px; height: 26px;
    color: var(--navy); font-size: 19px; gap: 5px;
  }
  .letterhead .brand-square { width: 7px; height: 7px; background: var(--green); }
  .letterhead .brand-tagline { left: 0; right: 0; top: 80px; font-size: 6.5px; }
  .letterhead-hashtag {
    position: absolute; left: 0; right: 0; top: 675px;
    text-align: center; color: var(--green);
    font-weight: 700; font-size: 11px;
  }
  .letterhead-footer {
    position: absolute; left: 0; right: 0; bottom: 0;
    height: 32px;
    background: var(--green);
    border-top: 3px solid var(--navy);
    color: var(--paper);
    font-size: 8px;
    display: flex; align-items: center; justify-content: center; gap: 4px;
    white-space: nowrap;
  }
  .letterhead-footer .icon { width: 7px; height: 7px; }
</style>
</head>
<body>

<section class="card card-front" aria-label="Business card front">
  <div class="brand-name"><span class="brand-square"></span>KAJU</div>
  <div class="brand-tagline">Transportation and Logistics Services</div>
  <div class="divider"></div>
  <div class="contact">
    <div class="contact-name">DANA REYES</div>
    <div class="contact-title">President</div>
    <div class="contact-address">4170 North Canyon Ridge Road<br>Mesa, AZ 85201</div>
    <div class="contact-line">
      <svg class="icon" viewBox="0 0 10 10"><path d="M2 0.5l2 2-1 1.3c.6 1.3 1.6 2.3 2.9 2.9l1.3-1 2 2-1.3 1.8C4.5 9 1 5.5.5 1.8z" fill="#82c341"/></svg>
      480-555-0192
    </div>
    <div class="contact-line">
      <svg class="icon" viewBox="0 0 10 10"><rect x="0.5" y="2" width="9" height="6" fill="#82c341"/><path d="M0.5 2l4.5 3.5L9.5 2" fill="none" stroke="#fff" stroke-width="0.9"/></svg>
      info@kajufreightco.example
    </div>
    <div class="contact-line">
      <svg class="icon" viewBox="0 0 10 10" fill="none" stroke="#82c341" stroke-width="0.9"><circle cx="5" cy="5" r="4.3"/><ellipse cx="5" cy="5" rx="1.9" ry="4.3"/><path d="M0.7 5h8.6M1.5 2.8h7M1.5 7.2h7"/></svg>
      www.kajufreightco.example
    </div>
  </div>
  <div class="hashtag-band">#ALLKAJU</div>
</section>

<section class="card card-back" aria-label="Business card back">
  <div class="brand-name"><span class="brand-square"></span>KAJU</div>
  <div class="website">www.kajufreightco.example</div>
</section>

<section class="letterhead" aria-label="Letterhead">
  <div class="brand-name"><span class="brand-square"></span>KAJU</div>
  <div class="brand-tagline">Transportation and Logistics Services</div>
  <div class="letterhead-hashtag">#ALLKAJU</div>
  <div class="letterhead-footer">
    <span>4170 North Canyon Ridge Road, Mesa, AZ 85201</span>
    <svg class="icon" viewBox="0 0 10 10"><path d="M2 0.5l2 2-1 1.3c.6 1.3 1.6 2.3 2.9 2.9l1.3-1 2 2-1.3 1.8C4.5 9 1 5.5.5 1.8z" fill="#fff"/></svg>
    <span>480-555-0192</span>
    <svg class="icon" viewBox="0 0 10 10"><rect x="0.5" y="2" width="9" height="6" fill="#fff"/><path d="M0.5 2l4.5 3.5L9.5 2" fill="none" stroke="#82c341" stroke-width="0.9"/></svg>
    <span>info@kajufreightco.example</span>
    <svg class="icon" viewBox="0 0 10 10" fill="none" stroke="#fff" stroke-width="0.9"><circle cx="5" cy="5" r="4.3"/><ellipse cx="5" cy="5" rx="1.9" ry="4.3"/><path d="M0.7 5h8.6M1.5 2.8h7M1.5 7.2h7"/></svg>
    <span>www.kajufreightco.example</span>
  </div>
</section>

</body>
</html>
```